Form With Marla - Health and Wellness Business Card and Logo

I need a business card design with a logo for my business you can check out at www.formwithmarla.net. I want something more original, simplistic, and memorable than the basic logo I have on my site currently. I am a health and wellness coach and I offer mindset coaching and nutrition plans. I like the colour teal and dark grey/black for my theme colours. I emphasize growth, longterm change, and the whole package of "healthy mind, healthy body, healthy life". I had played around the idea of intertwining 3 M's or incorporating growth (leaves etc.) into my design. I want my expertise and experience to show through. In one glance I want people to understand with confidence I can help them accomplish anything they set their minds to. I look forward to seeing what everyone comes up with!

Industry/Entity Type

Health And Wellness

Contact Information for Business Card

Form With Marla
Marla Prentiss
BSc, Health & Wellness Coach
"Manifest your best"
www.formwithmarla.net
formwithmarla@quillpost.net
472-618-9043

Colors
33b8a4
ffffff
333333
000000

Requirements
Must have
• A memorable and unique logo for my business!
Nice to have
• Could have the phrase "Are you unhappy with your body and state of health?" or "It takes the right skills to develop habits in order to create long term change. I can help you get there."

```html
<!DOCTYPE html>
<html lang="en">
<head>
<meta charset="utf-8">
<title>Form With Marla — Business Card</title>
<link rel="stylesheet" href="https://fonts.googleapis.com/css2?family=Open+Sans:wght@400;700&family=Questrial&display=swap">
<style>
  :root {
    --backdrop: #3b3b3b;
    --card-dark: #1e1e1e;
    --card-light: #ffffff;
    --ink: #333333;
    --ink-soft: #555555;
    --paper: #ffffff;
  }
  * { box-sizing: border-box; margin: 0; padding: 0; }
  html, body {
    width: 1200px; height: 1000px; overflow: hidden;
    background: var(--backdrop);
  }
  .canvas { position: relative; width: 1200px; height: 1000px; }

  .card { position: absolute; border-radius: 22px; overflow: hidden; }

  /* Front (dark) */
  .card--front {
    left: 215px; top: 30px; width: 770px; height: 430px;
    background: var(--card-dark); color: var(--paper);
    display: flex; flex-direction: column; align-items: center;
  }
  .front__mark {
    margin-top: 118px;
    font-family: "Open Sans", sans-serif; font-weight: 700;
    font-size: 40px; letter-spacing: 1px; line-height: 1;
  }
  .front__rule {
    width: 290px; height: 1px; background: var(--paper);
    margin-top: 14px; opacity: .8;
  }
  .front__wordmark {
    font-family: "Questrial", sans-serif; font-size: 36px;
    margin-top: 4px; letter-spacing: .5px;
  }
  .front__tagline {
    margin-top: 78px;
    font-family: "Open Sans", sans-serif; font-size: 17px;
    letter-spacing: 6px;
  }

  /* Back (white) */
  .card--back {
    left: 100px; top: 490px; width: 880px; height: 480px;
    background: var(--card-light); color: var(--ink);
  }
  .back__tab {
    position: absolute; left: 0; top: 140px;
    width: 14px; height: 44px; background: var(--ink);
    border-radius: 0 6px 6px 0;
  }
  .back__wordmark {
    position: absolute; left: 72px; top: 44px;
    font-family: "Questrial", sans-serif; font-size: 50px; color: #1a1a1a;
  }
  .back__name {
    position: absolute; left: 72px; top: 138px;
    font-family: "Open Sans", sans-serif; font-weight: 700;
    font-size: 30px; letter-spacing: .5px; text-transform: uppercase;
  }
  .back__title {
    position: absolute; left: 72px; top: 180px;
    font-family: "Open Sans", sans-serif; font-weight: 700;
    font-size: 15px; color: var(--ink-soft);
  }
  .contacts {
    position: absolute; left: 72px; top: 245px; list-style: none;
    font-family: "Open Sans", sans-serif; font-size: 19px; color: var(--ink-soft);
  }
  .contacts li { display: flex; align-items: center; height: 30px; }
  .contacts svg { width: 16px; height: 16px; margin-right: 14px; fill: var(--ink); }
  .contacts .strong { color: #111; }
  .back__mark {
    position: absolute; right: 60px; bottom: 48px;
    font-family: "Open Sans", sans-serif; font-weight: 700;
    font-size: 30px; color: var(--ink);
  }
</style>
</head>
<body>
<main class="canvas">
  <section class="card card--front">
    <div class="front__mark">Form With Marla</div>
    <div class="front__rule"></div>
    <div class="front__wordmark">form with marla</div>
    <div class="front__tagline">"Manifest your best"</div>
  </section>

  <section class="card card--back">
    <div class="back__tab"></div>
    <div class="back__wordmark">form with marla</div>
    <div class="back__name">Marla Prentiss</div>
    <div class="back__title">BSc, Health &amp; Wellness Coach</div>
    <ul class="contacts">
      <li>
        <svg viewBox="0 0 16 16" aria-hidden="true"><path d="M3 1h3l1.5 4-2 1.3a9 9 0 0 0 4.2 4.2L11 8.5l4 1.5v3a2 2 0 0 1-2 2A13 13 0 0 1 1 3a2 2 0 0 1 2-2z"/></svg>
        472-618-9043
      </li>
      <li>
        <svg viewBox="0 0 16 16" aria-hidden="true"><path d="M1 3h14v10H1z M1 3l7 6 7-6" fill="none" stroke="#333" stroke-width="1.6"/></svg>
        formwithmarla@quillpost.net
      </li>
      <li>
        <svg viewBox="0 0 16 16" aria-hidden="true"><circle cx="8" cy="8" r="7"/></svg>
        www.<span class="strong">formwithmarla</span>.net
      </li>
      <li>
        <svg viewBox="0 0 16 16" aria-hidden="true"><rect x="1" y="1" width="14" height="14" rx="3"/></svg>
        @marlaprentiss
      </li>
    </ul>
    <div class="back__mark">Form With Marla</div>
  </section>
</main>
</body>
</html>
```